Hop Bright Meadow Business Website Branding

Looking for a wordpress template design with CSS and HTML encoding. Current website can be seen at hopbrightmeadow.example.

WE ARE CURRENTLY IN PROCESS GETTING A LOGO DESIGN... I HAVE INCLUDED THE TOP POTENTIAL DESIGNS FOR REFERENCE TO HELP UNDERSTAND WHAT STYLE WE ARE LOOKING FOR...
NOTE: THE “PEBBLE CREW” LOGO WAS A PREVIOUS COMPANY WE OWNED SO YOU CAN GE A FEEL FOR THE TYPE OF DESIGNS WE HAVE USED IN THE PAST.

My blog will focus on making a connection with wild Florida, it’s wildlife, plants and animals... with an eye toward Florida conservation, nature adventure trips, and education... Content, photos and other merchandise will also be offered for sale.
I’m looking for a site design that incorporates Florida nature and wildlife/plants, with a fun “Old Florida” retro-adventure feel.
When they see this site it should speak to the import of natural Florida and the critical nature of the ecosystem here... while being instantly recognizable and iconic... IE: when I think of florida I think of water, plants, warmth, sunsets etc...

https://join.chatroomhub.example/t/lumexstudio-kzt4821/shared_invite/zt-pqwrt83m-hRnLvXaKoPzsYcB1Uq7JdM

Target Market(s)

Nature, Education, Conservation, Photography

Industry/Entity Type

Photographer

Coding

Coded - Design and coding required

Requirements
Must have
• Need to have site wide template design which generally includes a landing page and a general page template for other pages... Must include html and css encoding...
Should not have
• Any animals included in the site should be Florida native... IE: no African animals etc... This will require some research to ensure that if animals are included that they are part of the Florida ecosystem.

```html
<!DOCTYPE html>
<html lang="en">
<head>
<meta charset="utf-8">
<title>Hop Bright Meadow</title>
<link href="https://fonts.googleapis.com/css2?family=Abril+Fatface&family=Roboto:wght@400;500;700&display=swap" rel="stylesheet">
<style>
:root{
  --green:#5b9418;
  --green-dark:#4a7d10;
  --green-light:#6fa823;
  --orange:#f07a0c;
  --orange-light:#f7a21d;
  --ink:#1f1f1f;
  --text:#666;
  --white:#fff;
  --ring:#d4d4d4;
}
*{box-sizing:border-box;margin:0;padding:0}
html,body{width:1200px;height:4680px;overflow:hidden}
body{font-family:"Roboto",sans-serif;color:var(--text);background:var(--white)}
.page{position:relative;width:1200px;height:4680px;overflow:hidden}
.abs{position:absolute}
.heading{font-family:"Abril Fatface",serif;color:var(--ink);letter-spacing:-1.5px;text-transform:uppercase;font-weight:400}
.btn{position:absolute;display:flex;align-items:center;justify-content:center;gap:8px;background:linear-gradient(180deg,var(--orange-light),var(--orange));color:var(--white);font-weight:700;font-size:15px;border-radius:30px;text-transform:uppercase;box-shadow:0 3px 8px rgba(0,0,0,.2)}
.btn .dot{width:14px;height:14px;border-radius:50%;background:var(--white);display:inline-flex;align-items:center;justify-content:center}
.btn .dot::after{content:"";border-left:5px solid var(--orange);border-top:4px solid transparent;border-bottom:4px solid transparent;margin-left:2px}

/* header */
.site-header{position:absolute;top:0;left:0;width:1200px;height:109px;background:var(--white);z-index:3}
.nav{position:absolute;top:42px;left:0;width:1200px;font-size:14px;font-weight:500;color:var(--ink)}
.nav span{position:absolute;white-space:nowrap}
.nav .active{color:var(--green)}
.nav .active::after{content:"";position:absolute;left:0;right:0;top:24px;height:3px;background:var(--green)}
.search{position:absolute;left:1075px;top:44px;width:13px;height:13px;border:2.5px solid var(--ink);border-radius:50%}
.search::after{content:"";position:absolute;width:6px;height:2.5px;background:var(--ink);transform:rotate(45deg);left:8px;top:11px}
.logo-badge{position:absolute;left:82px;top:-36px;width:218px;height:218px;border-radius:50%;background:#f4f4f4;z-index:4;display:flex;align-items:center;justify-content:center;text-align:center;padding-top:40px;box-shadow:0 2px 8px rgba(0,0,0,.08)}
.brand-name{font-family:"Abril Fatface",serif;color:var(--green-dark);font-size:28px;line-height:1.05;text-transform:uppercase}

/* hero */
.hero{position:absolute;top:109px;left:0;width:1200px;height:720px;background:linear-gradient(180deg,#b8400a 0%,#e2650c 22%,#f79a1c 40%,#c2560a 55%,#5c2506 78%,#2a1204 100%)}
.hero-title{position:absolute;left:111px;top:292px;font-size:48px;color:var(--white);z-index:2}
.hero-text{position:absolute;left:111px;top:361px;width:480px;font-size:16px;line-height:27px;color:var(--white);z-index:2}
.slider-arrow{position:absolute;top:368px;width:34px;height:34px;border:2px solid var(--white);border-radius:50%;z-index:2}
.slider-arrow::after{content:"";position:absolute;top:10px;width:10px;height:10px;border-left:2px solid var(--white);border-bottom:2px solid var(--white)}
.slider-arrow.prev::after{left:13px;transform:rotate(45deg)}
.slider-arrow.next::after{left:8px;transform:rotate(-135deg)}
.wave{position:absolute;left:0;display:block}

/* about */
.about-ring{position:absolute;left:112px;top:819px;width:380px;height:380px;border-radius:50%;background:var(--green)}
.about-mask{position:absolute;left:128px;top:819px;width:380px;height:380px;border-radius:50%;background:var(--white)}
.about-photo{position:absolute;left:142px;top:824px;width:370px;height:370px;border-radius:50%;background:radial-gradient(circle at 55% 55%,#c98a6a 0%,#6e8fa8 45%,#9fb9cc 70%,#d7a97c 100%)}
.about-title{position:absolute;left:600px;top:840px;font-size:44px}
.about-text{position:absolute;left:600px;top:910px;width:490px;font-size:13.5px;line-height:25.8px}

/* nature adventure */
.nature{position:absolute;top:1300px;left:0;width:1200px;height:631px;background:linear-gradient(180deg,#63a01f,#4e8511)}
.section-title{position:absolute;left:0;width:1200px;text-align:center}
.nature .section-title{top:42px;font-size:40px;color:var(--white)}
.nature-intro{position:absolute;top:104px;left:0;width:1200px;text-align:center;font-size:13.5px;line-height:21px;color:var(--white)}
.adv-photo{position:absolute;top:191px;width:311px;height:245px}
.adv-card{position:absolute;top:400px;width:280px;height:145px;background:var(--white);border-radius:3px;text-align:center;padding:22px 14px 0;box-shadow:0 4px 12px rgba(0,0,0,.15)}
.adv-card h3{font-size:16px;font-weight:700;color:var(--ink);margin-bottom:14px}
.adv-card p{font-size:13.5px;line-height:20px}

/* specialised */
.special .section-title{top:2008px;font-size:40px}
.skill-icon{position:absolute;width:96px;height:96px;border-radius:50%;border:4px solid var(--green);background:var(--white)}
.skill-icon::after{content:"";position:absolute;left:8px;top:8px;width:72px;height:72px;border-radius:50%;background:var(--green)}
.skill-title{position:absolute;font-size:17px;font-weight:700;color:var(--ink);text-transform:uppercase}
.skill-text{position:absolute;width:300px;font-size:13.5px;line-height:23px}
.right-align{text-align:right}
.center-ring{position:absolute;left:454px;top:2161px;width:292px;height:292px;border-radius:50%;border:8px solid var(--ring);background:var(--white);display:flex;align-items:center;justify-content:center;text-align:center}
.center-ring .brand-name{font-size:32px}
.ring-dot{position:absolute;width:22px;height:22px;border-radius:50%;background:var(--white);border:4px solid var(--orange)}

/* quote */
.quote-text{position:absolute;top:2790px;left:150px;width:900px;text-align:center;color:var(--white);font-size:29px;line-height:44px;font-weight:500;text-transform:uppercase}
.quote-mark{position:absolute;font-family:"Abril Fatface",serif;font-size:60px;color:rgba(255,255,255,.35);line-height:1}

/* blog */
.blog .section-title{top:3112px;font-size:40px}
.post-card{position:absolute;background:var(--white);box-shadow:0 2px 12px rgba(0,0,0,.12);border-radius:3px}
.post-main{left:133px;top:3194px;width:445px;height:451px}
.post-main .thumb{position:absolute;left:7px;top:9px;width:431px;height:289px;background:linear-gradient(160deg,#3f6d1a,#8bb34a 50%,#c8a2d8 75%,#375e16)}
.post-main h3{position:absolute;top:315px;left:0;width:445px;text-align:center;font-size:15.5px;color:var(--ink);font-weight:700}
.meta{font-size:12.5px;color:var(--orange)}
.meta .sep{color:var(--text);margin:0 6px}
.meta .ico{display:inline-block;width:9px;height:9px;background:var(--green);margin-right:4px;border-radius:1px}
.post-main .meta{position:absolute;top:343px;width:445px;text-align:center}
.post-main p{position:absolute;top:373px;left:35px;width:375px;text-align:center;font-size:12px;line-height:22px}
.post-side{left:613px;width:445px;height:138px}
.post-side .thumb{position:absolute;left:7px;top:7px;width:154px;height:123px;background:linear-gradient(150deg,#2f5a14,#6f9a38 55%,#3e6a1a)}
.post-side h4{position:absolute;left:177px;top:10px;width:255px;font-size:12.5px;line-height:18px;color:var(--ink);font-weight:500}
.post-side .meta{position:absolute;left:177px;top:52px;font-size:12px}
.post-side p{position:absolute;left:177px;top:76px;width:255px;font-size:11.5px;line-height:19px}

/* gallery */
.gallery-title{position:absolute;left:111px;top:3718px;font-size:40px}
.gallery-arrow{position:absolute;top:3752px;width:11px;height:11px;border-left:3px solid var(--ink);border-bottom:3px solid var(--ink)}
.gallery-photo{position:absolute;top:3792px;width:233px;height:280px}

/* footer */
.footer-col{position:absolute;top:4370px;color:var(--white)}
.footer-col h5{font-size:16px;font-weight:700;margin-bottom:20px}
.footer-col li{list-style:none;font-size:13px;line-height:26px}
.contact-row{position:relative;padding-left:32px;font-size:13px;line-height:18px;margin-bottom:8px;width:240px}
.contact-row b{display:block;font-size:11px}
.contact-row .c-ico{position:absolute;left:0;top:2px;width:13px;height:13px;background:var(--orange);border-radius:2px}
.social{position:absolute;top:4520px;width:30px;height:30px;border-radius:50%}
.copyright{position:absolute;top:4636px;left:0;width:1200px;text-align:center;font-size:14px;color:var(--white)}
.to-top{position:absolute;left:1132px;top:4537px;width:34px;height:34px;border-radius:50%;background:var(--orange)}
.to-top::after{content:"";position:absolute;left:12px;top:14px;width:8px;height:8px;border-left:2px solid var(--white);border-top:2px solid var(--white);transform:rotate(45deg)}
</style>
</head>
<body>
<div class="page">

  <!-- Header -->
  <header class="site-header">
    <nav class="nav">
      <span class="active" style="left:504px">Home</span>
      <span style="left:577px">About Me</span>
      <span style="left:674px">Nature Adventure</span>
      <span style="left:826px">Gallery</span>
      <span style="left:905px">Blog</span>
      <span style="left:966px">Contact Us</span>
    </nav>
    <div class="search"></div>
  </header>
  <div class="logo-badge"><span class="brand-name">Hop Bright<br>Meadow</span></div>

  <!-- Hero -->
  <section class="hero" role="img" aria-label="Sunset over calm water with a wading heron silhouetted on the shore"></section>
  <h1 class="heading hero-title">Hop Bright Meadow</h1>
  <p class="hero-text">Come explore wild places and stunning scenery with me as I discover new and exciting eco-adventures</p>
  <div class="btn" style="left:113px;top:445px;width:183px;height:46px">Get Started <span class="dot"></span></div>
  <div class="slider-arrow prev" style="left:36px"></div>
  <div class="slider-arrow next" style="left:1126px"></div>
  <svg class="wave" style="top:650px" width="1200" height="220" viewBox="0 0 1200 220">
    <path d="M0 150 C250 40 500 50 720 85 C930 118 1100 60 1200 5 L1200 220 L0 220Z" fill="#5b9418"/>
    <path d="M0 220 L0 200 C260 90 500 90 720 118 C930 146 1100 90 1200 30 L1200 220Z" fill="#ffffff"/>
  </svg>

  <!-- About -->
  <div class="about-ring"></div>
  <div class="about-mask"></div>
  <div class="about-photo" role="img" aria-label="Portrait of the naturalist on a sunny beach"></div>
  <h2 class="heading about-title">About Me</h2>
  <p class="about-text">Hello nature lovers! I'm Marisol Tennant, a wildlife educator, Florida Master Naturalist, nature writer and photographer, busy mama of three kiddos, a playful Havanese puppy, two very chubby guinea pigs, and a giant tree frog. I have a passion for all things nature and I adore living in Southwest Florida. I will always be a California girl, but from the moment I set foot in Florida, its wild beauty stole my heart. For the past 23 years, I have been fortunate to have some very unique and special experiences</p>
  <div class="btn" style="left:600px;top:1122px;width:173px;height:45px">Learn More <span class="dot"></span></div>

  <!-- Nature Adventure -->
  <section class="nature">
    <h2 class="heading section-title">Nature Adventure</h2>
    <p class="nature-intro">Come explore wild places and stunning scenery with me as I discover new and exciting eco-adventures and learn about the rare and<br>unique wildlife and environments that make Florida so precious and extraordinary.</p>
    <div class="adv-photo" style="left:111px;background:linear-gradient(150deg,#3d5a1a,#e2323c 45%,#f0c23a 60%,#4a6a22)" role="img" aria-label="Red wild lilies in bloom"></div>
    <div class="adv-photo" style="left:445px;background:linear-gradient(150deg,#4b3f2a,#cdb89a 45%,#8a7050 70%,#3a3224)" role="img" aria-label="White peacock butterfly resting on leaf litter"></div>
    <div class="adv-photo" style="left:778px;background:linear-gradient(150deg,#5f7a6a,#2a2a2a 50%,#b7b1a0 80%)" role="img" aria-label="Black vulture perched on a fallen branch"></div>
    <div class="adv-card" style="left:127px"><h3>Lorem ipsum dolor sit</h3><p>Lorem ipsum dolor amet, consectetur adipiscing elit, sed eiusmod tempor incididunt ut labore et dolore</p></div>
    <div class="adv-card" style="left:461px"><h3>Lorem ipsum dolor sit</h3><p>Lorem ipsum dolor amet, consectetur adipiscing elit, sed eiusmod tempor incididunt ut labore et dolore</p></div>
    <div class="adv-card" style="left:793px"><h3>Lorem ipsum dolor sit</h3><p>Lorem ipsum dolor amet, consectetur adipiscing elit, sed eiusmod tempor incididunt ut labore et dolore</p></div>
  </section>

  <!-- Specialised -->
  <section class="special">
    <h2 class="heading section-title">Specialised In</h2>
    <div class="skill-icon" style="left:328px;top:2105px"></div>
    <div class="skill-title right-align" style="left:124px;top:2214px;width:300px">Wildlife Educator</div>
    <p class="skill-text right-align" style="left:124px;top:2246px">Lorem ipsum dolor sit consectetur adipiscing elit, sed eiusmod tempor ut labore</p>
    <div class="skill-icon" style="left:328px;top:2319px"></div>
    <div class="skill-title right-align" style="left:124px;top:2428px;width:300px">Florida Master Naturalist</div>
    <p class="skill-text right-align" style="left:124px;top:2460px">Lorem ipsum dolor sit consectetur adipiscing elit, sed eiusmod tempor ut labore</p>
    <div class="skill-icon" style="left:777px;top:2105px"></div>
    <div class="skill-title" style="left:778px;top:2214px">Nature Writer</div>
    <p class="skill-text" style="left:778px;top:2246px">Lorem ipsum dolor sit consectetur adipiscing elit, sed eiusmod tempor ut labore</p>
    <div class="skill-icon" style="left:777px;top:2319px"></div>
    <div class="skill-title" style="left:778px;top:2428px">Photographer</div>
    <p class="skill-text" style="left:778px;top:2460px">Lorem ipsum dolor sit consectetur adipiscing elit, sed eiusmod tempor ut labore</p>
    <div class="center-ring"><span class="brand-name">Hop Bright<br>Meadow</span></div>
    <div class="ring-dot" style="left:480px;top:2207px"></div>
    <div class="ring-dot" style="left:698px;top:2207px"></div>
    <div class="ring-dot" style="left:474px;top:2380px"></div>
    <div class="ring-dot" style="left:702px;top:2380px"></div>
  </section>

  <!-- Quote -->
  <svg class="wave" style="top:2582px" width="1200" height="510" viewBox="0 0 1200 510" role="img" aria-label="Warm orange haze of trees at dusk">
    <defs>
      <linearGradient id="quoteGlow" x1="0" y1="0" x2="1" y2="1">
        <stop offset="0" stop-color="#e8740c"/>
        <stop offset=".5" stop-color="#f3951a"/>
        <stop offset="1" stop-color="#e06a08"/>
      </linearGradient>
    </defs>
    <path d="M0 0 C300 80 800 90 1200 25 L1200 510 C900 400 300 400 0 505 Z" fill="url(#quoteGlow)"/>
  </svg>
  <span class="quote-mark" style="left:150px;top:2770px">“</span>
  <p class="quote-text">Look deep into nature, and then you will understand everything better.</p>
  <span class="quote-mark" style="left:786px;top:2838px">”</span>

  <!-- Blog -->
  <section class="blog">
    <h2 class="heading section-title">Our Blog</h2>
    <article class="post-card post-main">
      <div class="thumb" role="img" aria-label="Pink morning glory flowers among green grass"></div>
      <h3>Florida Master Naturalist Uplands Nature Journal</h3>
      <div class="meta"><span class="ico"></span>Oct 12, 2020<span class="sep">|</span><span class="ico"></span>Marisol</div>
      <p>September 24th-October 22nd, 2020 Communing with Nature at Fernway Cypress Preserve Trails *All photography by Marisol Tennant, October 2020</p>
    </article>
    <article class="post-card post-side" style="top:3194px">
      <div class="thumb" role="img" aria-label="Purple wildflower in grass"></div>
      <h4>Those who contemplate the beauty of the earth find reserves of</h4>
      <div class="meta"><span class="ico"></span>Nov 05, 2020<span class="sep">|</span><span class="ico"></span>Nora Pell</div>
      <p>Sed ut perspiciatis unde omnis iste natus sit voluptatem accusantium</p>
    </article>
    <article class="post-card post-side" style="top:3351px">
      <div class="thumb" role="img" aria-label="Red wildflower among green foliage"></div>
      <h4>Instructions for living a life. Pay attention. Be astonished. Tell about it.</h4>
      <div class="meta"><span class="ico"></span>Nov 05, 2020<span class="sep">|</span><span class="ico"></span>Ada Fenwick</div>
      <p>As a Florida Master Naturalist, environmental interpreter, and nature writer,</p>
    </article>
    <article class="post-card post-side" style="top:3507px">
      <div class="thumb" role="img" aria-label="Yellow wildflower among green leaves"></div>
      <h4>In every walk with nature, one receives far more than he seeks.”</h4>
      <div class="meta"><span class="ico"></span>Nov 05, 2020<span class="sep">|</span><span class="ico"></span>Elias Brook</div>
      <p>Fernway Cypress Trails in Oakhollow, Florida is part of a 60,000 acre conservation</p>
    </article>
  </section>

  <!-- Gallery -->
  <h2 class="heading gallery-title">Our Gallery</h2>
  <div class="gallery-arrow" style="left:1054px;transform:rotate(45deg)"></div>
  <div class="gallery-arrow" style="left:1076px;transform:rotate(-135deg)"></div>
  <div class="gallery-photo" style="left:111px;background:linear-gradient(150deg,#4a4a3a,#9a9a8a 50%,#3e3e2e)" role="img" aria-label="Gray moss hanging from a tree branch"></div>
  <div class="gallery-photo" style="left:360px;background:linear-gradient(150deg,#2e5312,#e3cf2a 45%,#4c7a1c)" role="img" aria-label="Yellow flowers on a green shrub"></div>
  <div class="gallery-photo" style="left:607px;background:linear-gradient(150deg,#7aa04a,#c9a48a 50%,#3a2818 75%,#6c8a3c)" role="img" aria-label="Hand holding a pine cone"></div>
  <div class="gallery-photo" style="left:856px;background:linear-gradient(150deg,#8a7a60,#4e6a2a 50%,#a08a6a)" role="img" aria-label="Palm trunk with green fronds"></div>

  <!-- Footer -->
  <svg class="wave" style="top:4127px" width="1200" height="553" viewBox="0 0 1200 553">
    <path d="M0 125 C220 150 360 215 600 205 C850 195 1000 50 1200 25 L1200 553 L0 553Z" fill="#f07a0c"/>
    <path d="M0 150 C220 175 360 240 600 232 C850 222 1000 80 1200 60 L1200 553 L0 553Z" fill="#5b9418"/>
  </svg>
  <div class="abs" style="left:134px;top:4380px;width:180px;text-align:center"><span class="brand-name" style="color:#fff;font-size:30px">Hop Bright<br>Meadow</span></div>
  <span class="social" style="left:170px;background:#3b5aa0"></span>
  <span class="social" style="left:209px;background:#2e9fe0"></span>
  <span class="social" style="left:248px;background:#9a35b0"></span>

  <div class="footer-col" style="left:409px">
    <h5>Quick Links</h5>
    <ul><li>Home</li><li>About</li><li>Nature Adventure</li><li>Gallery</li><li>Blog</li></ul>
  </div>
  <div class="footer-col" style="left:604px">
    <h5>About Company</h5>
    <ul><li>Terms of Use</li><li>Terms &amp; Condition</li><li>News</li><li>Contact Us</li><li>FAQ</li></ul>
  </div>
  <div class="footer-col" style="left:853px">
    <h5>Contact Us</h5>
    <div class="contact-row"><span class="c-ico"></span>Unit 1, 105 Lorem ipsum dolor sit amet, consectetur elit</div>
    <div class="contact-row"><span class="c-ico"></span><b>Phone</b>888 888 8888</div>
    <div class="contact-row"><span class="c-ico"></span><b>Fax</b>123 456 7890</div>
    <div class="contact-row"><span class="c-ico"></span><b>Email</b>info@hopbrightmeadow.example</div>
  </div>
  <div class="to-top"></div>
  <p class="copyright">2020 Copyright - hopbrightmeadow.example &nbsp;| All Rights Reserved</p>

</div>
</body>
</html>
```